business card design for a plumbing contractor

i need a double business card for a plumbing business, our initial service is residential Sewer Drain Cleaning.

Target Market(s)

other plumbing Business

Industry/Entity Type

Plumbing

Contact Information for Business Card

www.PipeworksTopMark.example- 5307218394-

Font styles to use
Serif

Colors
ec1f27
0455a3

```html
<!DOCTYPE html>
<html lang="en">
<head>
<meta charset="utf-8">
<title>Pipeworks Top Mark — Business Card</title>
<link href="https://fonts.googleapis.com/css2?family=Roboto+Condensed:wght@400;700&display=swap" rel="stylesheet">
<style>
  :root {
    --page: #ece9e4;
    --card-white: #ffffff;
    --brand-red: #de3a33;
    --ink-grey: #8a8580;
    --ink-dark: #4a4744;
    --shadow: rgba(40, 30, 20, 0.22);
  }
  * { box-sizing: border-box; margin: 0; padding: 0; }
  html, body {
    width: 1200px; height: 886px; overflow: hidden;
    background: var(--page);
    font-family: "Roboto Condensed", Arial, sans-serif;
  }
  .sheet {
    width: 1200px; height: 886px;
    display: flex; align-items: center; justify-content: center; gap: 60px;
  }
  .card {
    position: relative;
    width: 525px; height: 300px;
    border-radius: 18px;
    box-shadow: 0 10px 28px var(--shadow);
    overflow: hidden;
  }
  .card--front { background: var(--card-white); }
  .card--back { background: var(--brand-red); }

  .brand {
    position: absolute; left: 34px; top: 40px;
    display: flex; align-items: center; gap: 10px;
  }
  .brand__dot {
    width: 16px; height: 16px; border-radius: 50%;
    background: var(--brand-red);
  }
  .brand__name {
    font-weight: 700; font-size: 24px; line-height: 1;
    color: var(--ink-grey);
  }
  .feature-name {
    position: absolute; right: 34px; top: 58px;
    width: 220px; text-align: right;
    font-weight: 700; font-size: 44px; line-height: 1.02;
    color: var(--brand-red);
  }
  .person { position: absolute; left: 34px; bottom: 112px; }
  .person__name {
    font-size: 20px; font-weight: 400; color: var(--brand-red);
    text-transform: uppercase; letter-spacing: 0.2px;
  }
  .person__title {
    font-size: 14px; color: var(--ink-grey); text-transform: uppercase;
    margin-top: 2px;
  }
  .contacts {
    position: absolute; left: 34px; bottom: 28px;
    list-style: none; display: flex; flex-direction: column; gap: 6px;
  }
  .contacts__item {
    display: flex; align-items: center; gap: 8px;
    font-size: 14px; color: var(--ink-dark);
  }
  .contacts__icon { width: 14px; height: 14px; flex: none; }

  .back-brand {
    position: absolute; left: 0; right: 0; top: 100px;
    display: flex; align-items: center; justify-content: center; gap: 14px;
  }
  .back-brand__dot { width: 22px; height: 22px; border-radius: 50%; background: var(--card-white); }
  .back-brand__name { font-weight: 700; font-size: 36px; color: var(--card-white); }
  .services {
    position: absolute; left: 0; right: 0; bottom: 40px;
    text-align: center; font-size: 15px; color: var(--card-white);
    letter-spacing: 0.3px;
  }
</style>
</head>
<body>
<main class="sheet">
  <section class="card card--front" aria-label="Card front">
    <div class="brand">
      <span class="brand__dot"></span>
      <span class="brand__name">Pipeworks Top Mark</span>
    </div>
    <div class="feature-name">Pipeworks Top Mark</div>
    <div class="person">
      <p class="person__name">Dale Mercer</p>
      <p class="person__title">CEO/Founder</p>
    </div>
    <ul class="contacts">
      <li class="contacts__item">
        <svg class="contacts__icon" viewBox="0 0 24 24"><path fill="#de3a33" d="M6.6 10.8a15.1 15.1 0 0 0 6.6 6.6l2.2-2.2c.3-.3.7-.4 1-.2 1.1.4 2.3.6 3.6.6.6 0 1 .4 1 1V20c0 .6-.4 1-1 1A17 17 0 0 1 3 4c0-.6.4-1 1-1h3.5c.6 0 1 .4 1 1 0 1.3.2 2.5.6 3.6.1.3 0 .7-.2 1z"/></svg>
        5307218394
      </li>
      <li class="contacts__item">
        <svg class="contacts__icon" viewBox="0 0 24 24"><rect x="2" y="5" width="20" height="14" rx="2" fill="#de3a33"/><path d="M3 6l9 7 9-7" fill="none" stroke="#fff" stroke-width="1.8"/></svg>
        Dispatcher@PipeworksTopMark.example
      </li>
      <li class="contacts__item">
        <svg class="contacts__icon" viewBox="0 0 24 24"><circle cx="12" cy="12" r="10" fill="#de3a33"/><path d="M2 12h20M12 2c3 3 3 17 0 20M12 2c-3 3-3 17 0 20" fill="none" stroke="#fff" stroke-width="1.4"/></svg>
        www.PipeworksTopMark.example
      </li>
    </ul>
  </section>

  <section class="card card--back" aria-label="Card back">
    <div class="back-brand">
      <span class="back-brand__dot"></span>
      <span class="back-brand__name">Pipeworks Top Mark</span>
    </div>
    <p class="services">Sewer Drain Cleaning &nbsp;•&nbsp; Trenchless Pipe Installs</p>
  </section>
</main>
</body>
</html>
```